Valdo Capital

We need a corporate style website design for a new company based in Shenzhen's Qianhai Special Economic Development Zone, China. We provide a range of financial services to large international investment companies. Typically these companies invest over 5 million RMB. The company is part of a group that consists of NorthKilns, ValdoTrusts and ValdoEquity. Our location and gateway into Qianhai Special Economic Zone is our core advantage. We would like to see designs that Do Not use purple and orange. The website design should be similar to other websites in this family but different enough to give it a unique style (See attached website links for reference). The final design should communicate financial safety and growth. This website will act partly as a business chamber with connections to the government so we would like it to be diplomatic in style.

www.northkilns.example
www.valdotrusts.example

*Nevegation Bar
Should including Homepage, Financial Product, Team, News.
Could refer to www.valdotrusts.example

*Contact Details

Miss Lan
Address:E 728, North Block, KMO Centre, East Sector, Shenzhen Bright Science Campus
Telephone: +86 0755 63920417
Cellphone: +86 13957280316

* Social Media
Should be grouped like:
1. Weibo QRcode+ Weibo
2. Facebook, Twitter, Linkedin.

Industry/Entity Type

Investment

```html
<!DOCTYPE html>
<html lang="en">
<head>
<meta charset="utf-8">
<title>Valdo Capital</title>
<link href="https://fonts.googleapis.com/css2?family=Ubuntu:wght@400;500;700&family=Open+Sans:wght@400;600&display=swap" rel="stylesheet">
<style>
:root{
  --blue:#2b9bd1;
  --blue-bright:#1eaae6;
  --teal:#1c6f9a;
  --green-ring:#a4c64a;
  --ink:#222;
  --muted:#555;
  --nav-bg:#f6f8ef;
  --band:#f4f4f4;
  --line:#dcdcdc;
  --footer:#2b2b2b;
  --packet-title:#1f6f5a;
}
*{margin:0;padding:0;box-sizing:border-box}
html,body{width:1125px;height:1200px;overflow:hidden;background:#fff}
body{position:relative;font-family:Arial,Helvetica,sans-serif;color:var(--ink)}
.abs{position:absolute}

/* hero */
.hero{left:0;top:0;width:1125px;height:565px;
  background:radial-gradient(ellipse at 55% 45%,#cfe0f2 0%,#8fb5dd 35%,#3f6fa8 75%,#2b4f80 100%)}
.hero-people{left:270px;top:190px;width:610px;height:375px;border-radius:160px 160px 0 0;
  background:linear-gradient(180deg,rgba(120,140,165,.55),rgba(80,95,120,.75))}
.navbar{left:0;top:38px;width:1125px;height:41px;background:var(--nav-bg)}
.nav-item{top:38px;height:41px;line-height:41px;font-size:16px;color:#333;font-family:Arial,sans-serif}
.nav-item.active{background:var(--blue);color:#fff;padding:0 12px;left:562px;width:104px;text-align:center}
.brand{left:97px;top:13px;width:310px;height:91px;background:#fff;border-radius:10px;
  box-shadow:0 2px 6px rgba(0,0,0,.25);display:flex;align-items:center;padding-left:22px;gap:14px}
.brand-mark{width:38px;height:38px;border-radius:50%;background:var(--teal)}
.brand-name{font-family:"Ubuntu",sans-serif;font-weight:500;font-size:27px;color:#222}

.welcome-card{left:431px;top:352px;width:296px;height:212px;background:#f7f7f7;
  box-shadow:0 2px 8px rgba(0,0,0,.2);text-align:center;padding-top:22px}
.welcome-card .hello{font-family:"Ubuntu",sans-serif;font-size:23px;color:#333;letter-spacing:1px}
.welcome-card .title{font-family:"Ubuntu",sans-serif;font-size:30px;color:var(--blue-bright);letter-spacing:1px;margin-top:2px}
.welcome-card p{font-family:"Open Sans",sans-serif;font-size:12.2px;line-height:17px;color:#444;padding:10px 18px 0}

/* services */
.services{left:0;top:565px;width:1125px;height:268px;background:var(--band)}
.service{top:664px;width:206px;height:143px;background:var(--band);border:1px solid var(--line);text-align:center}
.service h3{font-family:"Open Sans",sans-serif;font-weight:600;font-size:16px;margin-top:39px;color:#222}
.service p{font-size:11.5px;line-height:19.5px;color:#555;text-align:left;padding:8px 9px 0}
.ring{top:601px;width:90px;height:90px}

/* packets */
.divider-v{width:1px;height:140px;top:860px;border-left:1px dotted #ccc}
.divider-h{left:153px;top:928px;width:810px;border-top:1px dotted #ccc}
.packet{width:230px}
.packet h4{font-family:"Ubuntu",sans-serif;font-weight:500;font-size:15px;color:var(--packet-title)}
.packet p{font-size:11.5px;line-height:13px;color:#444;letter-spacing:.3px}
.packet svg{position:absolute;left:-38px;top:0}

/* footer */
.footer{left:0;top:1029px;width:1125px;height:171px;background:var(--footer);border-top:5px solid var(--blue-bright)}
.f-head{font-family:"Ubuntu",sans-serif;font-size:18px;color:var(--blue-bright);top:1046px;letter-spacing:.5px}
.f-link{font-size:12px;color:#fff;display:flex;align-items:center;gap:10px}
.f-contact{font-family:"Ubuntu",sans-serif;font-size:14.5px;color:#fff;left:817px;letter-spacing:.4px}
.f-small{font-size:12px;color:#fff;top:1178px}
</style>
</head>
<body>

<div class="abs hero" role="img" aria-label="Blurred blue glass office towers behind a smiling business team"></div>
<div class="abs hero-people" role="img" aria-label="Group of five business people holding a welcome sign"></div>

<div class="abs navbar"></div>
<div class="abs nav-item active">Homepage</div>
<div class="abs nav-item" style="left:687px">Financial</div>
<div class="abs nav-item" style="left:796px">Product</div>
<div class="abs nav-item" style="left:900px">Team</div>
<div class="abs nav-item" style="left:983px">News</div>

<div class="abs brand"><span class="brand-mark"></span><span class="brand-name">Valdo Capital</span></div>

<div class="abs welcome-card">
  <div class="hello">Welcome to</div>
  <div class="title">VALDO CAPITAL</div>
  <p>Limited Shenzhen, located in Qianhai, China, is a new real-estate project investing operator, structuring urban-rural real-estate investment and development, and industrial fund investment.</p>
</div>

<div class="abs services"></div>

<div class="abs service" style="left:123px"><h3>Distribution</h3><p>sed diam nonumy eirmod tempor invid unt ut labore et dolore magna adipiocar scing consect etuer ali</p></div>
<div class="abs service" style="left:348px"><h3>Market Share</h3><p>sed diam nonumy eirmod tempor invid unt ut labore et dolore magna adipiocar scing consect etuer ali</p></div>
<div class="abs service" style="left:573px"><h3>HR Management</h3><p>sed diam nonumy eirmod tempor invid unt ut labore et dolore magna adipiocar scing consect etuer ali</p></div>
<div class="abs service" style="left:798px"><h3>Support 24/7</h3><p>sed diam nonumy eirmod tempor invid unt ut labore et dolore magna adipiocar scing consect etuer ali</p></div>

<svg class="abs ring" style="left:182px" viewBox="0 0 90 90"><circle cx="45" cy="45" r="43" fill="#fff" stroke="var(--green-ring)" stroke-width="3"/><circle cx="45" cy="45" r="38" fill="#f0f0f0"/><rect x="24" y="40" width="42" height="26" rx="2" fill="var(--teal)"/><rect x="29" y="22" width="28" height="18" fill="var(--teal)"/><rect x="32" y="52" width="26" height="5" fill="#fff"/></svg>
<svg class="abs ring" style="left:407px" viewBox="0 0 90 90"><circle cx="45" cy="45" r="43" fill="#fff" stroke="var(--green-ring)" stroke-width="3"/><circle cx="45" cy="45" r="38" fill="#f0f0f0"/><path d="M43 22 A24 24 0 1 0 67 46 L43 46 Z" fill="var(--teal)"/><path d="M47 18 A24 24 0 0 1 71 42 L47 42 Z" fill="var(--teal)"/></svg>
<svg class="abs ring" style="left:632px" viewBox="0 0 90 90"><circle cx="45" cy="45" r="43" fill="#fff" stroke="var(--green-ring)" stroke-width="3"/><circle cx="45" cy="45" r="38" fill="#f0f0f0"/><rect x="22" y="30" width="46" height="36" rx="3" fill="var(--teal)"/><rect x="38" y="20" width="14" height="14" rx="2" fill="var(--teal)"/><circle cx="34" cy="46" r="5" fill="#fff"/><rect x="27" y="53" width="14" height="7" fill="#fff"/><rect x="46" y="44" width="16" height="2" fill="#fff"/><rect x="46" y="50" width="16" height="2" fill="#fff"/><rect x="46" y="56" width="16" height="2" fill="#fff"/></svg>
<svg class="abs ring" style="left:857px" viewBox="0 0 90 90"><circle cx="45" cy="45" r="43" fill="#fff" stroke="var(--green-ring)" stroke-width="3"/><circle cx="45" cy="45" r="38" fill="#f0f0f0"/><circle cx="36" cy="34" r="8" fill="var(--teal)"/><rect x="24" y="44" width="22" height="22" rx="5" fill="var(--teal)"/><circle cx="53" cy="32" r="10" fill="var(--teal)"/><rect x="40" y="44" width="28" height="22" rx="6" fill="var(--teal)"/></svg>

<div class="abs divider-v" style="left:410px"></div>
<div class="abs divider-v" style="left:695px"></div>
<div class="abs divider-h"></div>

<div class="abs packet" style="left:187px;top:863px"><svg width="30" height="30" viewBox="0 0 30 30"><path d="M5 14 A10 10 0 0 1 25 14" fill="none" stroke="#4aa3d8" stroke-width="2"/><path d="M9 15 A6 6 0 0 1 21 15" fill="none" stroke="#4aa3d8" stroke-width="2"/><path d="M11 28 L15 14 L19 28 Z" fill="#333"/></svg><h4>Employee Packet</h4><p>Publish messages on desktop backgrounds. Change and sequence messages easily.</p></div>
<div class="abs packet" style="left:473px;top:863px"><svg width="30" height="30" viewBox="0 0 30 30"><circle cx="17" cy="13" r="10" fill="#bfe1f5" stroke="#2a7fc0" stroke-width="3"/><path d="M10 20 L3 27" stroke="#2a6fa0" stroke-width="5" stroke-linecap="round"/></svg><h4>Employee Packet</h4><p>Publish messages on desktop backgrounds. Change and sequence messages easily.</p></div>
<div class="abs packet" style="left:767px;top:863px"><svg width="30" height="30" viewBox="0 0 30 30"><rect x="5" y="10" width="20" height="18" rx="2" fill="#f5b400"/><path d="M10 11 V7 A5 5 0 0 1 20 7 V11" fill="none" stroke="#c48a00" stroke-width="2"/></svg><h4>Employee Packet</h4><p>Publish messages on desktop backgrounds. Change and sequence messages easily.</p></div>

<div class="abs packet" style="left:187px;top:940px"><svg width="30" height="30" viewBox="0 0 30 30"><circle cx="10" cy="10" r="5" fill="#e6a56a"/><rect x="3" y="16" width="14" height="10" rx="4" fill="#3b8fd6"/><circle cx="21" cy="12" r="5" fill="#e6a56a"/><rect x="14" y="18" width="14" height="10" rx="4" fill="#5cb85c"/></svg><h4>Employee Packet</h4><p>Publish messages on desktop backgrounds. Change and sequence messages easily.</p></div>
<div class="abs packet" style="left:473px;top:940px"><svg width="30" height="30" viewBox="0 0 30 30"><rect x="3" y="14" width="10" height="8" rx="1" fill="#f2c200"/><rect x="17" y="4" width="10" height="8" rx="1" fill="#f2c200"/><rect x="17" y="19" width="10" height="8" rx="1" fill="#f2c200"/><path d="M13 18 H15 V8 H17 M15 18 V23 H17" fill="none" stroke="#888" stroke-width="1.5"/></svg><h4>Employee Packet</h4><p>Publish messages on desktop backgrounds. Change and sequence messages easily.</p></div>
<div class="abs packet" style="left:767px;top:939px"><svg width="32" height="30" viewBox="0 0 32 30"><rect x="6" y="4" width="24" height="6" rx="2" fill="#9a9a9a"/><rect x="6" y="12" width="24" height="6" rx="2" fill="#8a8a8a"/><rect x="6" y="20" width="24" height="6" rx="2" fill="#7a7a7a"/><circle cx="8" cy="20" r="7" fill="#8dc63f"/><path d="M8 16 V24 M4 20 H12" stroke="#fff" stroke-width="2"/></svg><h4>Employee Packet</h4><p>Publish messages on desktop backgrounds. Change and sequence messages easily.</p></div>

<div class="abs footer"></div>
<div class="abs f-head" style="left:115px">Annual Report &amp; Financial Statement</div>
<div class="abs f-head" style="left:516px">Useful links</div>
<div class="abs f-head" style="left:816px">Stay in touch</div>

<div class="abs f-link" style="left:116px;top:1090px"><svg width="14" height="16" viewBox="0 0 14 16"><rect x="2" y="1" width="10" height="14" fill="#6aa6d8"/><rect x="0" y="3" width="6" height="13" fill="#e0c060"/></svg>Annual Reports &amp; Accounts 2011 PDF (1MB)</div>
<div class="abs f-link" style="left:116px;top:1113px"><svg width="14" height="16" viewBox="0 0 14 16"><rect x="2" y="1" width="10" height="14" fill="#6aa6d8"/><rect x="0" y="3" width="6" height="13" fill="#e0c060"/></svg>Full Year Results Presentation PDF [4.3Mb]</div>
<div class="abs f-link" style="left:116px;top:1136px"><svg width="14" height="16" viewBox="0 0 14 16"><rect x="2" y="1" width="10" height="14" fill="#6aa6d8"/><rect x="0" y="3" width="6" height="13" fill="#e0c060"/></svg>AGM Notice 2012 PDF [145Kb]</div>

<div class="abs f-link" style="left:515px;top:1091px"><svg width="13" height="13" viewBox="0 0 13 13"><rect width="13" height="13" fill="var(--blue-bright)"/><path d="M5 4 L8 6.5 L5 9" fill="none" stroke="#fff" stroke-width="1.3"/></svg>Shareholders Information</div>
<div class="abs f-link" style="left:515px;top:1115px"><svg width="13" height="13" viewBox="0 0 13 13"><rect width="13" height="13" fill="var(--blue-bright)"/><path d="M5 4 L8 6.5 L5 9" fill="none" stroke="#fff" stroke-width="1.3"/></svg>Reports and presentations</div>
<div class="abs f-link" style="left:515px;top:1140px"><svg width="13" height="13" viewBox="0 0 13 13"><rect width="13" height="13" fill="var(--blue-bright)"/><path d="M5 4 L8 6.5 L5 9" fill="none" stroke="#fff" stroke-width="1.3"/></svg>Worldwide Locations</div>

<div class="abs f-contact" style="top:1085px">Tel: +27 83 512 0746</div>
<div class="abs f-contact" style="top:1111px">Fax: +27 86 431 9025</div>
<div class="abs f-contact" style="top:1137px">Email: info@valdocapital.example</div>

<div class="abs f-small" style="left:102px">ValdoCapital © 2014&nbsp; All Right reserved</div>
<div class="abs f-small" style="left:787px">Terms &amp; conditions &nbsp;| &nbsp;Privacy Policy &nbsp; | &nbsp; Sitemap</div>

</body>
</html>
```